Letterhead and matching envelope design for a dental office

We need a new stationary design, letterhead and envelope #10, for a dental office in Denver area. We are called Bright Harbor Dental. We want a simple and minimalistic design but not a boring design. I wish to have one good point that makes it look professional. I have attached our logo. Feel free to use either one. I want the design for letterhead and envelope look like a "matching pair" but not look the same. The envelope doesn't have to be white and it will have an address window on bottom left.

Target Market(s)

everyone who visits dentist (adults)

Industry/Entity Type

Dental

Font styles to use
Other font styles liked:
• close to font on logo or something that matches well

Requirements
Must have
• professional
• simple, minimalistic
• unique point that stands out
Nice to have
• matching but not same design for letterhead and envelope
Should not have
• not look like all the other boring designs
• no flowery, distracting feats

```html
<!DOCTYPE html>
<html lang="en">
<head>
<meta charset="utf-8">
<title>Bright Harbor Dental — Letterhead</title>
<link rel="stylesheet" href="https://fonts.googleapis.com/css2?family=Cinzel:wght@600&family=Open+Sans:wght@300;400&display=swap">
<style>
  :root {
    --backdrop: #b7d9cf;
    --paper: #ffffff;
    --brand-green: #1f9a3e;
    --brand-green-dark: #157a2f;
    --band-grey: #a7a7ab;
    --swoosh-grey: #ececee;
    --swoosh-line: #e2e2e5;
    --leaf-tint: #e3efe3;
    --text-muted: #7a7a7f;
    --text-dark: #2f2f33;
  }
  html, body {
    margin: 0;
    padding: 0;
    width: 1200px;
    height: 784px;
    overflow: hidden;
    background: var(--backdrop);
  }
  .letterhead {
    position: absolute;
    left: 338px;
    top: 22px;
    width: 524px;
    height: 740px;
    background: var(--paper);
    box-shadow: 0 6px 18px rgba(40, 80, 70, 0.18);
    overflow: hidden;
  }
  .swoosh {
    position: absolute;
    inset: 0;
    width: 100%;
    height: 100%;
  }
  .leaf-watermark {
    position: absolute;
    left: 70px;
    top: 520px;
    width: 130px;
    height: 70px;
    border-radius: 50%;
    background: radial-gradient(ellipse at center, var(--leaf-tint) 0%, rgba(227,239,227,0) 72%);
  }
  .brand-mark {
    position: absolute;
    top: 46px;
    right: 40px;
    display: flex;
    align-items: center;
    gap: 10px;
  }
  .brand-mark__dot {
    width: 14px;
    height: 14px;
    border-radius: 50%;
    background: var(--brand-green);
  }
  .brand-mark__name {
    font-family: "Cinzel", serif;
    font-weight: 600;
    font-size: 15px;
    letter-spacing: 2.5px;
    color: var(--brand-green);
  }
  .footer {
    position: absolute;
    left: 22px;
    right: 22px;
    bottom: 26px;
    font-family: "Open Sans", sans-serif;
  }
  .footer__contacts {
    display: flex;
    flex-wrap: nowrap;
    justify-content: space-between;
    align-items: center;
    gap: 5px;
    font-weight: 300;
    font-size: 6.8px;
    color: var(--text-muted);
    white-space: nowrap;
  }
  .contact {
    display: inline-flex;
    align-items: center;
    gap: 3px;
  }
  .contact__icon {
    width: 8px;
    height: 8px;
    flex: none;
  }
  .footer__name {
    margin: 9px 0 5px;
    font-family: "Cinzel", serif;
    font-weight: 600;
    font-size: 11px;
    letter-spacing: 2px;
    color: var(--brand-green);
  }
  .footer__registration {
    font-weight: 400;
    font-size: 7.6px;
    color: var(--text-dark);
  }
  .edge-band {
    position: absolute;
    left: 0;
    right: 0;
    bottom: 0;
    height: 9px;
    display: flex;
  }
  .edge-band__grey { width: 12%; background: var(--band-grey); }
  .edge-band__green { flex: 1; background: linear-gradient(90deg, var(--brand-green), var(--brand-green-dark)); }
</style>
</head>
<body>
  <main class="letterhead">
    <svg class="swoosh" viewBox="0 0 524 740" preserveAspectRatio="none" aria-hidden="true">
      <path d="M0 420 C 160 470, 300 600, 380 731 L 0 731 Z" fill="var(--swoosh-grey)" opacity="0.6"/>
      <path d="M524 300 C 470 230, 420 150, 400 0 L 524 0 Z" fill="var(--swoosh-grey)" opacity="0.5"/>
      <path d="M0 400 C 150 450, 290 580, 360 731" fill="none" stroke="var(--swoosh-line)" stroke-width="14"/>
      <path d="M0 445 C 140 480, 250 590, 300 731" fill="none" stroke="var(--swoosh-line)" stroke-width="3"/>
      <path d="M524 280 C 480 220, 430 140, 418 0" fill="none" stroke="var(--swoosh-line)" stroke-width="10"/>
      <path d="M524 320 C 470 250, 410 160, 395 0" fill="none" stroke="var(--swoosh-line)" stroke-width="2"/>
    </svg>

    <div class="leaf-watermark" role="img" aria-label="Faint leaf emblem watermark"></div>

    <div class="brand-mark">
      <span class="brand-mark__dot"></span>
      <span class="brand-mark__name">BRIGHT HARBOR DENTAL</span>
    </div>

    <footer class="footer">
      <div class="footer__contacts">
        <span class="contact">
          <svg class="contact__icon" viewBox="0 0 10 10"><circle cx="5" cy="5" r="5" fill="var(--brand-green)"/><path d="M5 2.2a1.7 1.7 0 0 1 1.7 1.7C6.7 5.2 5 7.6 5 7.6S3.3 5.2 3.3 3.9A1.7 1.7 0 0 1 5 2.2z" fill="#fff"/></svg>
          120 Harbor Lane, Suite 300, Denver, CO 80202
        </span>
        <span class="contact">
          <svg class="contact__icon" viewBox="0 0 10 10"><circle cx="5" cy="5" r="5" fill="var(--brand-green)"/><path d="M3.3 2.6l1 .9-.5.8a4 4 0 0 0 1.9 1.9l.8-.5.9 1-.7.7C5.2 7.3 2.7 4.8 2.6 3.3z" fill="#fff"/></svg>
          303.555.0148
        </span>
        <span class="contact">
          <svg class="contact__icon" viewBox="0 0 10 10"><circle cx="5" cy="5" r="5" fill="var(--brand-green)"/><rect x="3" y="2.6" width="4" height="2" fill="#fff"/><rect x="2.4" y="4.8" width="5.2" height="2.6" fill="#fff"/></svg>
          303.555.0149
        </span>
        <span class="contact">
          <svg class="contact__icon" viewBox="0 0 10 10"><circle cx="5" cy="5" r="5" fill="var(--brand-green)"/><rect x="2.5" y="3.3" width="5" height="3.4" fill="#fff"/><path d="M2.5 3.3L5 5.2 7.5 3.3" fill="none" stroke="var(--brand-green)" stroke-width="0.6"/></svg>
          hello@brightharbor.dental
        </span>
        <span class="contact">
          <svg class="contact__icon" viewBox="0 0 10 10"><circle cx="5" cy="5" r="5" fill="var(--brand-green)"/><circle cx="5" cy="5" r="2.6" fill="none" stroke="#fff" stroke-width="0.7"/><path d="M2.4 5h5.2M5 2.4v5.2" stroke="#fff" stroke-width="0.6"/></svg>
          www.brightharbor.dental
        </span>
      </div>
      <div class="footer__name">BRIGHT HARBOR DENTAL</div>
      <div class="footer__registration">Provider No. 482117W &nbsp;|&nbsp; ABN 51 824 753 556</div>
    </footer>

    <div class="edge-band">
      <div class="edge-band__grey"></div>
      <div class="edge-band__green"></div>
    </div>
  </main>
</body>
</html>
```